Business Card Design Project

i need a bussines car design
Velora Clinical Hypnotherapy

Daniel Wexford
Psychotherapy & Hypnosis

84261937 /0427591628

back of the card appoinment space.

file was provided on a PDF, LOgo , use the blu colorsa as well , elegant, clear,

Target Market(s)

young professional, caucasian , young mothers.

Industry/Entity Type

Business

```html
<!DOCTYPE html>
<html lang="en">
<head>
<meta charset="utf-8">
<title>Velora Hypnotherapy – Business Card</title>
<link rel="stylesheet" href="https://fonts.googleapis.com/css2?family=Questrial&display=swap">
<style>
  :root {
    --backdrop: #3b3b3d;
    --card: #ffffff;
    --brand-blue: #1f7fc4;
    --ink: #2f2f2f;
    --muted: #555555;
    --photo-light: #f3e6d8;
    --photo-mid: #d9bfa4;
  }
  * { box-sizing: border-box; margin: 0; padding: 0; }
  html, body {
    width: 1200px; height: 900px; overflow: hidden;
    background: var(--backdrop);
    font-family: "Questrial", "Century Gothic", sans-serif;
    color: var(--ink);
  }
  .stage {
    position: relative; width: 1200px; height: 900px;
    display: flex; justify-content: center; align-items: center; gap: 40px;
  }
  .card {
    position: relative; width: 520px; height: 300px;
    background: var(--card); border-radius: 16px; overflow: hidden;
    box-shadow: 0 6px 14px rgba(0,0,0,.45);
  }
  .brand { position: absolute; left: 28px; top: 28px; z-index: 2; }
  .brand-name {
    display: flex; align-items: center; gap: 10px;
    font-size: 23px; color: var(--brand-blue); line-height: 1; white-space: nowrap;
  }
  .brand-dot { width: 14px; height: 14px; border-radius: 50%; background: var(--brand-blue); }
  .brand-url {
    margin-top: 6px; padding-top: 3px; border-top: 1px solid var(--brand-blue);
    font-size: 10px; letter-spacing: 1.2px; color: var(--muted); white-space: nowrap;
  }
  /* front */
  .portrait {
    position: absolute; right: 0; top: 80px; width: 250px; height: 220px; z-index: 0;
    background: linear-gradient(160deg, var(--card) 10%, var(--photo-light) 55%, var(--photo-mid) 100%);
  }
  .person { position: absolute; left: 28px; top: 140px; z-index: 1; }
  .person-name { font-size: 24px; font-weight: 400; color: var(--brand-blue); line-height: 1.2; }
  .person-role { font-size: 15px; margin-top: 2px; }
  .member-badge {
    position: absolute; left: 258px; top: 146px; z-index: 1;
    width: 40px; height: 40px; border-radius: 50%;
    background: #c8d86a; border: 2px solid #b9b9b9;
  }
  .contacts { position: absolute; left: 28px; top: 224px; list-style: none; font-size: 14px; z-index: 1; }
  .contacts li { display: flex; align-items: center; gap: 7px; height: 19px; }
  .contacts svg { width: 11px; height: 11px; fill: var(--brand-blue); }
  /* back */
  .appointments { position: absolute; left: 42px; top: 86px; list-style: none; font-size: 16px; }
  .appointments li { display: flex; align-items: flex-end; height: 27px; white-space: nowrap; }
  .blank { display: inline-block; border-bottom: 1px solid var(--ink); height: 16px; }
  .notice { position: absolute; left: 42px; top: 238px; font-size: 10.5px; line-height: 1.3; color: var(--muted); }
  .registration { font-size: 12px; margin-top: 2px; }
</style>
</head>
<body>
<main class="stage">
  <section class="card card-front">
    <div class="brand">
      <div class="brand-name"><span class="brand-dot"></span>Velora Hypnotherapy</div>
      <div class="brand-url">www.veloraclinicalhypnotherapy.com.au</div>
    </div>
    <div class="portrait" role="img" aria-label="Portrait photograph of the therapist"></div>
    <div class="person">
      <h1 class="person-name">Daniel Wexford</h1>
      <p class="person-role">Psychotherapy &amp; Hypnosis</p>
    </div>
    <div class="member-badge" aria-hidden="true"></div>
    <ul class="contacts">
      <li><svg viewBox="0 0 10 10"><path d="M5 0a3.5 3.5 0 0 0-3.5 3.5C1.5 6 5 10 5 10s3.5-4 3.5-6.5A3.5 3.5 0 0 0 5 0zm0 5a1.4 1.4 0 1 1 0-2.8A1.4 1.4 0 0 1 5 5z"/></svg>148 Carrow St, Brenton</li>
      <li><svg viewBox="0 0 10 10"><path d="M2 0l2 2.5-1.2 1.3a6 6 0 0 0 3.4 3.4L7.5 6 10 8l-1.5 2C4 10 0 6 0 1.5z"/></svg>0427 591 628</li>
      <li><svg viewBox="0 0 10 10"><path d="M2.5 0h5a1 1 0 0 1 1 1v8a1 1 0 0 1-1 1h-5a1 1 0 0 1-1-1V1a1 1 0 0 1 1-1zm.5 1.5v6h4v-6z"/></svg>8426 1937</li>
    </ul>
  </section>

  <section class="card card-back">
    <div class="brand">
      <div class="brand-name"><span class="brand-dot"></span>Velora Hypnotherapy</div>
      <div class="brand-url">www.veloraclinicalhypnotherapy.com.au</div>
    </div>
    <ol class="appointments">
      <li>1.&nbsp;<span class="blank" style="width:32px"></span>am/pm&nbsp;<span class="blank" style="width:140px"></span>&nbsp;&nbsp;<span class="blank" style="width:24px"></span>/<span class="blank" style="width:26px"></span>/<span class="blank" style="width:26px"></span></li>
      <li>2.&nbsp;<span class="blank" style="width:32px"></span>am/pm&nbsp;<span class="blank" style="width:140px"></span>&nbsp;&nbsp;<span class="blank" style="width:24px"></span>/<span class="blank" style="width:26px"></span>/<span class="blank" style="width:26px"></span></li>
      <li>3.&nbsp;<span class="blank" style="width:32px"></span>am/pm&nbsp;<span class="blank" style="width:140px"></span>&nbsp;&nbsp;<span class="blank" style="width:24px"></span>/<span class="blank" style="width:26px"></span>/<span class="blank" style="width:26px"></span></li>
      <li>4.&nbsp;<span class="blank" style="width:32px"></span>am/pm&nbsp;<span class="blank" style="width:140px"></span>&nbsp;&nbsp;<span class="blank" style="width:24px"></span>/<span class="blank" style="width:26px"></span>/<span class="blank" style="width:26px"></span></li>
      <li>5.&nbsp;<span class="blank" style="width:32px"></span>am/pm&nbsp;<span class="blank" style="width:140px"></span>&nbsp;&nbsp;<span class="blank" style="width:24px"></span>/<span class="blank" style="width:26px"></span>/<span class="blank" style="width:26px"></span></li>
    </ol>
    <div class="notice">
      <p>To reschedule your appointment, please SMS or phone 0427 591 628<br>at least 24 hours prior to your allocated time. Thank you.</p>
      <p class="registration">NHRA Registration No. NPM058214</p>
    </div>
  </section>
</main>
</body>
</html>
```